The 22 Rules and Traps of House Lending or the 22 things that will derail your transaction and how to prevent them.

I am looking to do a series of 4 to 5 e-books that should have a consistent format and theme

The first of these should be entitled, "The 22 Rules and Traps of House Lending" That is similar in style to the attached e-book.
The attached e-book is pretty much the style that I am looking for, The same format can be followed. I have attached a black and white head shot image for the head shot areas that appears on page two of the attached e-book. I have also attached my company logo.
Please feel free to use the same or similar colors in my logo for the lay-out of the e-book. However please do not feel limited to those colors. - Feel free to use your imagination.

The content can be found here.

http://www.fredtheloanfox.example/loan-advice.php

For the final “About” page of the e-book - Please entitle it… About Fred the Loan Fox.
The content for the last page can be found in the attached document - Owen Thistlewood bio2

The first page is where the creativity come in

Requirements
Must have
• Note that this project is for one e-book - However, once the designer and format is chosen the remainder of the projects will be launched

```html
<!DOCTYPE html>
<html lang="en">
<head>
<meta charset="utf-8">
<title>The 22 Rules and Traps of House Lending – Page 4</title>
<link href="https://fonts.googleapis.com/css2?family=Jost:wght@400;600;700&family=Arimo:wght@400;700&family=Playfair+Display:wght@700&family=Cormorant+SC:wght@600;700&display=swap" rel="stylesheet">
<style>
  :root{
    --navy:#1f3a78;
    --badge:#23468e;
    --red:#e0261b;
    --callout:#3a64aa;
    --body:#2a2a2a;
    --paper:#ffffff;
  }
  html,body{margin:0;padding:0;width:900px;height:1200px;overflow:hidden;background:var(--paper);}
  .page{position:relative;width:900px;height:1200px;background:var(--paper);}
  .tip{position:absolute;left:0;width:900px;}
  .tip-badge{position:absolute;left:24px;top:0;width:52px;height:52px;border-radius:50%;background:var(--badge);
    color:#fff;font-family:"Playfair Display",serif;font-weight:700;font-size:30px;line-height:46px;text-align:center;}
  .tip-title{position:absolute;left:63px;top:6px;width:780px;margin:0;font-family:"Arimo",Arial,sans-serif;font-weight:400;
    font-size:29px;line-height:36px;color:var(--navy);text-indent:43px;}
  .tip-title .dont{color:var(--red);font-weight:700;}
  .tip-body{position:absolute;left:63px;width:780px;margin:0;font-family:"Jost",sans-serif;font-size:14.6px;line-height:20.5px;color:var(--body);}
  .tip-callout{position:absolute;left:63px;width:770px;margin:0;font-family:"Jost",sans-serif;font-weight:700;font-size:18.4px;line-height:30px;color:var(--callout);}
  .footer{position:absolute;left:63px;top:1092px;width:776px;height:56px;display:flex;align-items:center;}
  .brand{display:flex;align-items:center;gap:8px;font-family:"Jost",sans-serif;font-weight:700;font-size:19px;color:var(--navy);}
  .brand-mark{width:14px;height:14px;background:var(--navy);}
  .footer-rule{width:1.5px;height:36px;background:var(--navy);margin:0 12px;}
  .footer-title,.footer-licence{font-family:"Cormorant SC",serif;font-weight:700;font-size:15.5px;color:var(--navy);letter-spacing:.3px;}
  .footer-title b{font-size:20px;}
  .footer-licence{margin-left:55px;}
  .page-number{margin-left:auto;width:24px;height:26px;background:var(--navy);color:#fff;font-family:"Jost",sans-serif;font-size:16px;line-height:26px;text-align:center;}
</style>
</head>
<body>
<main class="page">

  <section class="tip" style="top:46px;">
    <div class="tip-badge">04</div>
    <h2 class="tip-title"><span class="dont">Don’t</span> apply for any new credit during the underwriting process.</h2>
    <p class="tip-body" style="top:96px;">Some borrowers can get caught up in a buying fervor when purchasing a house. They want to furnish their new home and get appliances for their new kitchen. Some are temped to apply for new credit. Every time someone applies for credit, the new creditor will obtain a copy of your credit report to establish creditworthiness.</p>
    <p class="tip-callout" style="top:186px;">These inquires can adversely effect a borrower’s credit score, which in turn may adversely effect the underwriting of your loan, and possibly the final rate of your mortgage.</p>
  </section>

  <section class="tip" style="top:354px;">
    <div class="tip-badge">05</div>
    <h2 class="tip-title"><span class="dont">Don’t</span> get multiple inquiries during the underwriting process.</h2>
    <p class="tip-body" style="top:94px;">Similar to the Don’t mentioned above is to avoid having multiple mortgage companies obtain multiple copies of your credit while researching the best mortgage company to do your loan for you. While I generally encourage shopping for the best rate and fee structure for your purchase or refinance, it is generally a bad idea to allow multiple mortgage companies to obtain copies of your credit as this can adversely effect your credit score.</p>
    <p class="tip-callout" style="top:210px;">When in doubt it is always best to ask the advise of your mortgage professional.</p>
  </section>

  <section class="tip" style="top:622px;">
    <div class="tip-badge">06</div>
    <h2 class="tip-title"><span class="dont">Don’t</span> incur any new debt during the underwriting process.</h2>
    <p class="tip-body" style="top:92px;">This don’t is a continuation of the last one. When you apply for and obtain new credit you create a underwriting double-whammy. Not only have you incurred an unnecessary credit inquiry on your credit report, you have increased your debt load, which can adversely affect your debt-to-income ratio.</p>
    <p class="tip-callout" style="top:174px;">If your loan is at the edge of the lender’s allowable debt-to-income ratio and you apply for and obtain new credit, that new debt may be just enough to result in a loan denial. The best rule of thumb is to resist the urge to buy new furniture or appliances until after your mortgage transaction has closed.</p>
  </section>

  <footer class="footer">
    <div class="brand"><span class="brand-mark"></span>Harborline Lending</div>
    <div class="footer-rule"></div>
    <div class="footer-title">The <b>22</b> Rules and Traps of House Lending</div>
    <div class="footer-licence">Licence MLO#40218</div>
    <div class="page-number">4</div>
  </footer>

</main>
</body>
</html>
```